Website redesign - vorelmik.com

We are looking to do a full redesign of vorelmik.com. Need a designer to come up overall layout and 3 specific pages and 3 different hero images.
Wireframes for the 3 pages are attached as well as site images. You don't have to follow the wireframes exactly, but instead the wireframe is there to show you the information that needs to be on each page. Feel free to rearrange as needed.
Our target market is self taught engineers. So definitely I want a more casual feel to it. I'm ok with fun bold colors as well. Really like websites that have the infinite scroll look/feel to them.
Looking to find a designer who will produce HTML and potentially even implement the HTML into our site checked in code.
HTML Code should be responsive/mobile first leveraging Bootstrap 4.
Attached files include:
0) Wireframe PDF
https://files.plomwerk.net/d/7Kx2pQmW9zLr4TbN8vYc3HsE5fJ/view?mode=share
1) Vorelmik Images zip 1
https://files.plomwerk.net/d/4Gt8nRvB2wQx6MkZ1pLd9YaC7hU/view?mode=share
2) Vorelmik Images zip 2
https://files.plomwerk.net/d/9Jw3sTcF5yNv1HqX8rKb2ZeM6dP/view?mode=share
Target Market(s)
I sell DIY Waterproof Electronics enclosures. Target audience is self taught DIY engineers
Coding
Coded - Design and coding required
Number of Pages Required
3 page
Colors
Designer to choose colors to be used in the design.
Look and feel

```html
<!DOCTYPE html>
<html lang="en">
<head>
<meta charset="utf-8">
<title>Vorelmik – Waterproof Project Boxes</title>
<link href="https://fonts.googleapis.com/css2?family=Mulish:wght@400;600;700&display=swap" rel="stylesheet">
<style>
:root{
  --orange:#ff6a00;
  --yellow:#f5f200;
  --ink:#1c1c1c;
  --body:#555;
  --grey-bg:#f3f3f3;
  --line:#cfcfcf;
  --footer:#0a0a0a;
}
*{margin:0;padding:0;box-sizing:border-box}
html,body{width:1200px;height:3853px;overflow:hidden}
body{font-family:'Mulish',sans-serif;color:var(--ink);background:#fff;position:relative}
.abs{position:absolute}
.btn{position:absolute;background:var(--orange);color:#fff;font-weight:600;text-transform:uppercase;display:flex;align-items:center;justify-content:center;text-decoration:none}
.media{position:absolute}
.dots{position:absolute;display:flex;gap:8px;transform:translateX(-50%)}
.dots span{width:11px;height:11px;border-radius:50%;background:#111}
.dots span.open{background:#fff;border:2px solid #111}

/* header */
.site-header{position:absolute;left:0;top:0;width:1200px;height:82px;background:#fff}
.brand{position:absolute;left:75px;top:18px;font-size:34px;font-weight:700;color:var(--ink);letter-spacing:.5px}
.main-nav{position:absolute;left:283px;top:33px;display:flex;gap:31px;font-size:16px}
.main-nav a{color:#222;text-decoration:none}
.main-nav a.active{color:var(--orange)}
.nav-auth{position:absolute;top:29px;height:27px;font-size:13px;display:flex;align-items:center;justify-content:center}
.sign-in{left:917px;width:91px;background:var(--yellow);color:#222}
.sign-up{left:1029px;width:93px;background:var(--orange);color:#fff}

/* hero */
.hero{position:absolute;left:0;top:82px;width:1200px;height:498px;background:linear-gradient(135deg,#8a6a48 0%,#a88560 45%,#6e5a47 100%)}
.hero h1{position:absolute;left:73px;top:124px;width:680px;font-size:38px;line-height:46px;font-weight:600;color:#fff}
.hero .btn{left:73px;top:286px;width:183px;height:54px;font-size:21px}

/* designer */
.designer h2{left:537px;top:668px;width:560px;font-size:35px;line-height:49px;font-weight:600}
.designer p{left:537px;top:778px;width:585px;font-size:17px;line-height:30px;color:var(--body);text-align:justify}
.designer .btn{left:537px;top:910px;width:153px;height:43px;font-size:17px}

/* kits */
.kits{position:absolute;left:0;top:1058px;width:1200px;height:398px;background:var(--grey-bg)}
.kits h2{position:absolute;left:73px;top:68px;width:515px;font-size:34px;line-height:45px;font-weight:500;text-align:justify}
.kits .btn{left:73px;top:221px;width:141px;height:41px;font-size:16px}

/* makers */
.makers h2{left:531px;top:1548px;width:600px;font-size:31px;line-height:44px;font-weight:600}
.feature-list{position:absolute;left:535px;top:1646px;list-style:none;font-size:19px;color:#444}
.feature-list li{height:44.5px;display:flex;align-items:center;gap:16px}
.feature-list svg{flex:none}
.makers .btn{left:533px;top:1831px;width:139px;height:41px;font-size:16px}

/* testimonials */
.reviews{position:absolute;left:0;top:1975px;width:1200px;height:411px;background:var(--grey-bg)}
.reviews h2{position:absolute;left:0;top:46px;width:1200px;text-align:center;font-size:37px;font-weight:600}
.quote{position:absolute;top:125px;width:466px;height:189px;background:#fff}
.quote p{position:absolute;left:14px;top:12px;width:436px;font-size:19px;line-height:33px;color:#333;text-align:justify}
.quote cite{position:absolute;left:18px;top:143px;font-style:normal;font-size:21px;font-weight:600}
.quote svg{position:absolute;left:0;bottom:-18px}

/* gallery */
.gallery-title{left:0;top:2478px;width:1200px;text-align:center;font-size:37px;font-weight:600}
.build{position:absolute;width:328px}
.build .frame{width:328px;height:293px;border:2px solid #ddd;background:#fff;padding:10px}
.build .frame div{width:100%;height:100%}
.build h3{margin-top:18px;text-align:center;font-size:18px;line-height:28px;font-weight:600;color:#222}

/* footer */
.site-footer{position:absolute;left:0;top:3795px;width:1200px;height:58px;background:var(--footer);color:#fff;font-size:16px}
.site-footer .copy{position:absolute;left:73px;top:19px}
.site-footer .follow{position:absolute;right:82px;top:17px;display:flex;align-items:center;gap:14px}
.site-footer .follow span.icon{width:20px;height:18px;background:#fff;display:inline-block}
</style>
</head>
<body>

<header class="site-header">
  <div class="brand">Vorelmik</div>
  <nav class="main-nav">
    <a class="active" href="#">HOME</a>
    <a href="#">GET STARTED</a>
    <a href="#">DESIGNS</a>
    <a href="#">FAQS</a>
    <a href="#">VIDEOS</a>
    <a href="#">CONTACT US</a>
  </nav>
  <a class="nav-auth sign-in">SIGN IN</a>
  <a class="nav-auth sign-up">SIGN UP</a>
</header>

<section class="hero" role="img" aria-label="Flat-packed project box panels, screwdriver, pliers and hardware bags on a wooden workbench">
  <h1>Waterproof Project Box assembled in half the time (and it looks twice as good)</h1>
  <a class="btn">Get Started</a>
  <div class="dots" style="left:600px;top:454px"><span></span><span class="open"></span><span></span></div>
</section>

<section class="designer">
  <div class="media" style="left:78px;top:681px;width:381px;height:273px;background:linear-gradient(135deg,#b7b7b7,#e4e4e4 60%,#9a9a9a)" role="img" aria-label="Video preview of a finished aluminium project box with power cables"></div>
  <svg class="abs" style="left:247px;top:796px" width="44" height="44" viewBox="0 0 44 44"><circle cx="22" cy="22" r="21" fill="#fff"/><path d="M17 13 L31 22 L17 31 Z" fill="#222"/></svg>
  <h2 class="abs">Customize your Project Box using our Designer</h2>
  <p class="abs">Lorem ipsum dolor sit amet, consectetur adipiscing elit, sed do eiusmod tempor incididunt ut labore et dolore magna aliqua. Ut enim ad minim veniam, quis nostrud exercitation ullamco laboris nisi ut aliquip ex ea commodo</p>
  <a class="btn">Get Started</a>
</section>

<section class="kits">
  <h2>Mounting Kits for all the popular water proof project boxes with many sizes to choose from</h2>
  <a class="btn">Get Started</a>
  <div class="media" style="left:639px;top:40px;width:112px;height:298px;background:linear-gradient(160deg,#556b4e,#2c3a2a)" role="img" aria-label="Circuit board mounted on a plate"></div>
  <div class="media" style="left:751px;top:48px;width:287px;height:290px;background:linear-gradient(160deg,#ffffff,#e2e2e2)" role="img" aria-label="White waterproof enclosure with latches"></div>
  <div class="media" style="left:1038px;top:42px;width:98px;height:300px;background:linear-gradient(200deg,#4f6a48,#242f22)" role="img" aria-label="Wired controller board inside enclosure"></div>
  <div class="dots" style="left:895px;top:349px"><span></span><span class="open"></span><span></span></div>
</section>

<section class="makers">
  <div class="media" style="left:73px;top:1557px;width:382px;height:315px;background:linear-gradient(135deg,#b08b62,#c8a57c 55%,#8f7658)" role="img" aria-label="Mounting plate with single-board computers, power supply and screws"></div>
  <h2 class="abs">Vorelmik waterproof project boxes were built by makers for makers</h2>
  <ul class="feature-list">
    <li><svg width="11" height="11" viewBox="0 0 11 11"><path d="M1 1 L10 5.5 L1 10 L4 5.5 Z" fill="#ff6a00"/></svg>Design to your specifications</li>
    <li><svg width="11" height="11" viewBox="0 0 11 11"><path d="M1 1 L10 5.5 L1 10 L4 5.5 Z" fill="#ff6a00"/></svg>Maker components: Korvino, Bramblecore Pi, Steadvolt Power</li>
    <li><svg width="11" height="11" viewBox="0 0 11 11"><path d="M1 1 L10 5.5 L1 10 L4 5.5 Z" fill="#ff6a00"/></svg>Detailed build instructions, videos, walkthroughs</li>
    <li><svg width="11" height="11" viewBox="0 0 11 11"><path d="M1 1 L10 5.5 L1 10 L4 5.5 Z" fill="#ff6a00"/></svg>DIY made to look professional</li>
  </ul>
  <a class="btn">Get Started</a>
</section>

<section class="reviews">
  <h2>What our Customers Have to Say</h2>
  <blockquote class="quote" style="left:112px">
    <p>“Great work at a reasonable cost. I can’t recommend them enough. If you’re doing custom boxes for light shows, this is where you go.”</p>
    <cite>Marta K</cite>
    <svg width="293" height="20" viewBox="0 0 293 20"><path d="M0 0 H283 L293 8 H14 L0 20 Z" fill="#ff6a00"/></svg>
  </blockquote>
  <blockquote class="quote" style="left:619px">
    <p>“Fantastic service/product.. whether you simply generate the design and do all of the fabrication yourself or simply order the kits.”</p>
    <cite>Owen L</cite>
    <svg width="293" height="20" viewBox="0 0 293 20"><path d="M0 0 H283 L293 8 H14 L0 20 Z" fill="#ff6a00"/></svg>
  </blockquote>
  <div class="dots" style="left:600px;top:362px"><span></span><span class="open"></span><span></span></div>
</section>

<h2 class="abs gallery-title">See Real Examples from our Customers</h2>

<div class="build" style="left:73px;top:2584px"><div class="frame"><div role="img" aria-label="Controller boards on stacked acrylic plates" style="background:linear-gradient(160deg,#f4f4f4,#6c7d5f 50%,#2a2a2a)"></div></div><h3>KTR BX8-72 W/ P16V3 +<br>EXPANSION BOARD</h3></div>
<div class="build" style="left:435px;top:2584px"><div class="frame"><div role="img" aria-label="Power supply mounted above controller board" style="background:linear-gradient(160deg,#f4f4f4,#9a9a9a 50%,#2a2a2a)"></div></div><h3>KTR BX8-72 W/ P16V3 +<br>EXPANSION BOARD</h3></div>
<div class="build" style="left:799px;top:2584px"><div class="frame"><div role="img" aria-label="Two power supplies with red wiring on a plate" style="background:linear-gradient(170deg,#f6f6f6,#a7a7a7 55%,#2b2b2b)"></div></div><h3>KTR BX8-72 W/ P16V3 +<br>EXPANSION BOARD</h3></div>

<div class="build" style="left:73px;top:2980px"><div class="frame"><div role="img" aria-label="Compact mounting plate with fan and terminal blocks" style="background:linear-gradient(160deg,#f4f4f4,#7b7b7b 50%,#2a2a2a)"></div></div><h3>KTR BX8-72 W/ P16V3 +<br>EXPANSION BOARD</h3></div>
<div class="build" style="left:435px;top:2980px"><div class="frame"><div role="img" aria-label="Board stack on black base with standoffs" style="background:linear-gradient(160deg,#f4f4f4,#6a7a5e 45%,#232323)"></div></div><h3>KTR BX8-72 W/ P16V3 +<br>EXPANSION BOARD</h3></div>
<div class="build" style="left:799px;top:2980px"><div class="frame"><div role="img" aria-label="Fully wired multi-board assembly" style="background:linear-gradient(160deg,#f4f4f4,#5f7355 45%,#262626)"></div></div><h3>KTR BX8-72 W/ P16V3 +<br>EXPANSION BOARD</h3></div>

<div class="build" style="left:73px;top:3387px"><div class="frame"><div role="img" aria-label="Aluminium project box with power cables" style="background:linear-gradient(160deg,#ffffff,#c9c9c9 55%,#3a3a3a)"></div></div><h3>KTR BX8-72 W/ P16V3 +<br>EXPANSION BOARD</h3></div>
<div class="build" style="left:435px;top:3387px"><div class="frame"><div role="img" aria-label="Closed white waterproof enclosure" style="background:linear-gradient(160deg,#ffffff,#e6e6e6 55%,#c9c9c9)"></div></div><h3>KTR BX8-72 W/ P16V3 +<br>EXPANSION BOARD</h3></div>
<div class="build" style="left:799px;top:3387px"><div class="frame"><div role="img" aria-label="Small white waterproof enclosure" style="background:linear-gradient(160deg,#ffffff,#e8e8e8 55%,#cdcdcd)"></div></div><h3>KTR BX8-72 W/ P16V3 +<br>EXPANSION BOARD</h3></div>

<footer class="site-footer">
  <div class="copy">Copyright 2019-2020 @ vorelmik designer.</div>
  <div class="follow">Follow Us: <span class="icon"></span><span class="icon"></span></div>
</footer>

</body>
</html>
```